Need business card with a logo for a hearing aid sales and audiology business. We have two Hearing Instrument Specialists and one Audiologist on staff. Over 25 years in business. Locally owned and operated. Financing available. Most insurances accepted.

Summit Audio Wellness LLC
48730 W Larchmont, Suite 7
Spokane, WA 99281
509-617-2084
www.summitaudiowell.example

Manager
Tobias Kerrell HIS COHC
License #71829046

Target Market(s)

50yr old + people with a hearing loss.

Industry/Entity Type

Business

Contact Information for Business Card

48730 W Larchmont, Suite 7
Spokane, WA 99281
509-617-2084
www.summitaudiowell.example

Manager
Tobias Kerrell HIS COHC
NLVE #71829046

Font styles to use
Serif
Sans Serif

Requirements
Must have
• Business name, Tobias's name and title(s) and contact information, License #, web address

```html
<!DOCTYPE html>
<html lang="en">
<head>
<meta charset="utf-8">
<title>Summit Audio Wellness – Business Card</title>
<link href="https://fonts.googleapis.com/css2?family=Open+Sans:wght@400;600;700&display=swap" rel="stylesheet">
<style>
  :root {
    --brand-blue: #1d3f95;
    --ink: #333333;
    --card: #ffffff;
    --backdrop: #e9e6e2;
  }
  * { margin: 0; padding: 0; box-sizing: border-box; }
  html, body { width: 1200px; height: 1000px; overflow: hidden; }
  body {
    position: relative;
    background: var(--backdrop);
    font-family: "Open Sans", Arial, sans-serif;
    color: var(--ink);
  }
  .business-card {
    position: absolute;
    left: 265px;
    width: 665px;
    height: 397px;
    background: var(--card);
    border-radius: 22px;
    overflow: hidden;
  }
  .business-card.front { top: 73px; }
  .business-card.back { top: 532px; }

  .brand-lockup {
    position: absolute;
    left: 33px;
    top: 62px;
    display: flex;
    align-items: center;
    gap: 12px;
  }
  .brand-dot {
    width: 22px; height: 22px;
    border-radius: 50%;
    background: var(--brand-blue);
  }
  .brand-name {
    font-size: 28px;
    font-weight: 600;
    color: var(--brand-blue);
    letter-spacing: -0.3px;
  }

  .company-details {
    position: absolute;
    left: 33px;
    top: 232px;
    font-size: 16px;
    line-height: 21px;
  }
  .company-name { color: var(--brand-blue); font-weight: 600; }
  .company-name .entity { font-weight: 400; }
  .contact-list { margin-top: 14px; list-style: none; }
  .contact-list li { display: flex; align-items: center; gap: 6px; height: 24px; }
  .contact-list svg { width: 16px; height: 16px; fill: var(--brand-blue); }

  .person {
    position: absolute;
    right: 31px;
    top: 194px;
    text-align: right;
    font-size: 16px;
    line-height: 25px;
  }
  .person-name {
    font-size: 21px;
    font-weight: 700;
    color: var(--brand-blue);
    margin-bottom: 8px;
  }
  .person-name .credentials { font-size: 16px; font-weight: 400; }
</style>
</head>
<body>

<article class="business-card front">
  <div class="brand-lockup">
    <span class="brand-dot"></span>
    <span class="brand-name">Summit Audio Wellness</span>
  </div>
  <div class="company-details">
    <p class="company-name">Summit Audio Wellness <span class="entity">LLC</span></p>
    <p>48730 W Larchmont, Suite 7</p>
    <p>Spokane, WA 99281</p>
    <ul class="contact-list">
      <li><svg viewBox="0 0 16 16" aria-hidden="true"><path d="M2 6c0-2 2-3 6-3s6 1 6 3v1h-3V6H5v1H2zM4 8h8l2 5H2z"/></svg>509-617-2084</li>
      <li><svg viewBox="0 0 16 16" aria-hidden="true"><circle cx="8" cy="8" r="6.5" fill="none" stroke="#1d3f95" stroke-width="1.6"/><path d="M4 5c2 1 3 0 4 2s-1 3 0 5M9 3c0 2 2 2 3 4"/></svg>www.summitaudiowell.example</li>
    </ul>
  </div>
  <div class="person">
    <p class="person-name">TOBIAS KERRELL <span class="credentials">HIS COHC</span></p>
    <p>Manager</p>
    <p>License #71829046</p>
  </div>
</article>

<article class="business-card back">
  <div class="brand-lockup">
    <span class="brand-dot"></span>
    <span class="brand-name">Summit Audio Wellness</span>
  </div>
  <div class="company-details">
    <p class="company-name">Summit Audio Wellness <span class="entity">LLC</span></p>
    <p>48730 W Larchmont, Suite 7</p>
    <p>Spokane, WA 99281</p>
    <ul class="contact-list">
      <li><svg viewBox="0 0 16 16" aria-hidden="true"><path d="M2 6c0-2 2-3 6-3s6 1 6 3v1h-3V6H5v1H2zM4 8h8l2 5H2z"/></svg>509-617-2084</li>
      <li><svg viewBox="0 0 16 16" aria-hidden="true"><circle cx="8" cy="8" r="6.5" fill="none" stroke="#1d3f95" stroke-width="1.6"/><path d="M4 5c2 1 3 0 4 2s-1 3 0 5M9 3c0 2 2 2 3 4"/></svg>www.summitaudiowell.example</li>
    </ul>
  </div>
  <div class="person">
    <p class="person-name">TOBIAS KERRELL <span class="credentials">HIS COHC</span></p>
    <p>Manager</p>
    <p>License #71829046</p>
  </div>
</article>

</body>
</html>
```